Stationery Design Project

We need a stationery design for our Norwegian trucking company. We have existed for about 15 years and our 12 drivers uses relatively new vehicles to transport goods around in northern Norway. Long distance routes with fresh fish og food transport is our main operations.

We have already made alogo that's printed on our trucks. The logo and a picture of our trucks is attached. I think the logo i crappy, but since its already in use, changing it is not an option in this round. Still using a better colour scheme in the overall stationery and more interesting fonts is possible (altso in the logo).

Company details:
Name: Kjelvraket AS
Organisation nr 873 615 309
Post adress: 8642 Raudvik

I like minimalism and simplicity. I am avalibly for questions in normal GMT working hours either here or on mail: ivar@fjordlast.no

Reason: Hi. Im extending the deadline because I needed some time to find a vector file of our logo. Sorry for the inconvenience

Hi, and thanks for all your interest in the project. Some updates:

-          I have decided to commit to using one of the designs. Some designer will get the payment.

-          I have extended the deadline with 24 hours since I needed some time to find our firms vector logo (a slow Swedish man was holding me up)

-          We will not choose a design before the deadline. No need to rush.

-          We have received a lot of great design and think there is a need to specified the product we want to make:

o   Business Card for all our employers. I just need the design and will duplicate with the correct numbers and name myself. The information on should be: Logo, employer’s name, Phone number, email, website, Postal number and address. Use this as a template: logo, Leif Brattvoll, 47382066, Leif@fjordlast.no,, fjordlast.no, 8642 Raudvik. The order and placement of the information is your creative decision.

o   Stickers to put on the goods we travel. On the sticker the should be the following information: Logo, phone number, Tekst and link: Fraktæ av Kjelvraket. Ke du syns? Fjordlast.no/tilbakemelding (this means: Handled by Kjelvraket. What do you think Fjordlast.no/feedback -à the link will be a feedback form). The placement the information and size is your creative decision with some stings: we have been thinking of using Drukko for printing and see that a size about 6x6 cm, 8x5 or something like that. (with 3000 copies our budget is 200 punds). Any suggestions of other suppliers are welcome. Drukko price calculator http://www.drukkolabelhouse.co.uk/digital-litho-printing/printing-labels-tags/stickers/

o   Letterhead with logo, address, phone number and organizational number.

o   Envelopes with logo,address, phone number and organizational number.

Have a nice day.

 

 

• Using the blue colour in the logo and using a similar graphic approch.

```html
<!DOCTYPE html>
<html lang="no">
<head>
<meta charset="utf-8">
<title>Kjelvraket AS – stationery</title>
<link rel="stylesheet" href="https://fonts.googleapis.com/css2?family=Roboto:wght@400;700&family=Tinos:wght@400;700&display=swap">
<style>
:root{
  --backdrop:#2b1d16;
  --paper:#ffffff;
  --blue:#1b78c8;
  --navy:#0e55ad;
  --deep:#0a3f92;
  --pale:#e6edf6;
  --ink:#1f3f7a;
  --rule:#c9d3e0;
}
*{box-sizing:border-box;margin:0;padding:0}
html,body{width:1200px;height:417px;overflow:hidden}
body{background:var(--backdrop);position:relative;font-family:"Roboto",Arial,sans-serif;color:var(--ink)}
.item{position:absolute;background:var(--paper);overflow:hidden}
.wordmark{display:flex;align-items:center;gap:3px;font-family:"Roboto",Arial,sans-serif;font-weight:700;color:var(--navy);white-space:nowrap;line-height:1}
.wordmark .dot{border-radius:50%;background:var(--navy);flex:none}
.wordmark.light{color:#fff}
.wordmark.light .dot{background:#fff}
.wave{position:absolute;left:0;bottom:0;width:100%}
.tiny{font-size:3.6px;color:var(--ink);white-space:nowrap}
.tiny.white{color:#fff}

/* stickers */
.sticker{position:absolute;display:flex;flex-direction:column;align-items:center;justify-content:center;text-align:center;font-family:"Tinos","Times New Roman",serif;gap:1px}
.sticker .msg{font-size:4px;line-height:1.25}
.sticker .phone{font-size:8.5px;display:flex;align-items:center;gap:2px}
.sticker .phone svg{width:6px;height:6px}
.sticker.rect{width:70px;height:46px;border-radius:4px}
.sticker.round{width:56px;height:56px;border-radius:50%}
.sticker.white{background:var(--paper);color:var(--ink);border:2px dashed var(--blue)}
.sticker.blue{background:var(--navy);color:#fff;border:2px solid #fff;outline:1px solid var(--navy)}
.sticker.blue .wordmark{color:#fff}
.sticker.blue .wordmark .dot{background:#fff}

/* letterheads */
.letter{width:196px;height:253px}
.letter .wordmark.top{position:absolute;top:18px;left:50%;transform:translateX(-50%);font-size:12px}
.letter .watermark{position:absolute;left:50%;transform:translateX(-50%);font-size:24px;color:var(--pale)}
.letter .watermark .dot{background:var(--pale);width:16px;height:16px}
.letter-footer{position:absolute;bottom:6px;left:0;right:0;display:flex;justify-content:center;gap:9px}
.wave-contact{position:absolute;right:6px;bottom:6px;display:flex;flex-direction:column;gap:1px;align-items:flex-start}

/* fax */
.fax .wordmark{position:absolute;top:9px;left:8px;font-size:11px}
.fax .head-contact{position:absolute;top:12px;left:148px;display:flex;flex-direction:column;gap:1.5px}
.fax h1{position:absolute;top:41px;left:15px;font-size:11px;font-weight:700;color:#111}
.fax-fields{position:absolute;top:67px;left:15px;width:168px;display:grid;grid-template-columns:1fr 1fr;column-gap:8px;row-gap:6.5px}
.fax-fields span{font-size:3.4px;color:#333;border-bottom:0.5px solid var(--rule);padding-bottom:1px}
.fax-checks{position:absolute;top:117px;left:15px;right:12px;display:flex;justify-content:space-between}
.fax-checks span{font-size:3.2px;color:#333;display:flex;align-items:center;gap:2px}
.fax-checks span::before{content:"";width:3px;height:3px;border:0.5px solid #888}

/* envelopes */
.envelope{width:217px}

/* business cards */
.card{width:125px;height:72px;display:flex;flex-direction:column;align-items:center;justify-content:center;gap:6px}
.card .url{font-size:4.5px;letter-spacing:1.2px}
.card.blue{background:var(--blue);color:#fff}
.card.navy{background:var(--deep);color:#fff}
.card.front{width:139px}
.card.front .wordmark{position:absolute;top:12px;left:10px;font-size:11px}
.card.front .name{position:absolute;top:40px;left:8px;font-size:5px;font-weight:700;color:var(--navy)}
</style>
</head>
<body>

<!-- stickers -->
<div class="sticker rect white" style="left:28px;top:98px">
  <div class="wordmark" style="font-size:6px"><span class="dot" style="width:4px;height:4px"></span>Kjelvraket</div>
  <div class="msg">Fraktæ av Kjelvraket. Ke du syns?<br>Fjordlast.no/tilbakemelding</div>
  <div class="phone"><svg viewBox="0 0 10 10"><rect width="10" height="10" rx="1.5" fill="var(--blue)"/><path d="M3 2.5l1.2 1.6-.7.8a4 4 0 0 0 1.8 1.8l.8-.7 1.6 1.2-.9 1c-2.6-.2-4.6-2.2-4.8-4.8z" fill="#fff"/></svg>47-382-066</div>
</div>
<div class="sticker rect blue" style="left:113px;top:98px">
  <div class="wordmark" style="font-size:6px"><span class="dot" style="width:4px;height:4px"></span>Kjelvraket</div>
  <div class="msg">Fraktæ av Kjelvraket. Ke du syns?<br>Fjordlast.no/tilbakemelding</div>
  <div class="phone"><svg viewBox="0 0 10 10"><rect width="10" height="10" rx="1.5" fill="#fff"/><path d="M3 2.5l1.2 1.6-.7.8a4 4 0 0 0 1.8 1.8l.8-.7 1.6 1.2-.9 1c-2.6-.2-4.6-2.2-4.8-4.8z" fill="var(--navy)"/></svg>47-382-066</div>
</div>
<div class="sticker rect white" style="left:28px;top:180px;border-style:dotted">
  <div class="wordmark" style="font-size:6px"><span class="dot" style="width:4px;height:4px"></span>Kjelvraket</div>
  <div class="msg">Fraktæ av Kjelvraket. Ke du syns?<br>Fjordlast.no/tilbakemelding</div>
  <div class="phone"><svg viewBox="0 0 10 10"><rect width="10" height="10" rx="1.5" fill="var(--blue)"/><path d="M3 2.5l1.2 1.6-.7.8a4 4 0 0 0 1.8 1.8l.8-.7 1.6 1.2-.9 1c-2.6-.2-4.6-2.2-4.8-4.8z" fill="#fff"/></svg>47-382-066</div>
</div>
<div class="sticker rect blue" style="left:113px;top:180px;border-radius:8px">
  <div class="wordmark" style="font-size:6px"><span class="dot" style="width:4px;height:4px"></span>Kjelvraket</div>
  <div class="msg">Fraktæ av Kjelvraket. Ke du syns?<br>Fjordlast.no/tilbakemelding</div>
  <div class="phone"><svg viewBox="0 0 10 10"><rect width="10" height="10" rx="1.5" fill="#fff"/><path d="M3 2.5l1.2 1.6-.7.8a4 4 0 0 0 1.8 1.8l.8-.7 1.6 1.2-.9 1c-2.6-.2-4.6-2.2-4.8-4.8z" fill="var(--navy)"/></svg>47-382-066</div>
</div>
<div class="sticker round white" style="left:34px;top:262px">
  <div class="wordmark" style="font-size:5.5px"><span class="dot" style="width:3.5px;height:3.5px"></span>Kjelvraket</div>
  <div class="msg" style="font-size:3.4px">Fraktæ av Kjelvraket.<br>Ke du syns?<br>Fjordlast.no/tilbakemelding</div>
  <div class="phone" style="font-size:5.5px">47-382-066</div>
</div>
<div class="sticker round blue" style="left:123px;top:262px">
  <div class="wordmark" style="font-size:5.5px"><span class="dot" style="width:3.5px;height:3.5px"></span>Kjelvraket</div>
  <div class="msg" style="font-size:3.4px">Fraktæ av Kjelvraket.<br>Ke du syns?<br>Fjordlast.no/tilbakemelding</div>
  <div class="phone" style="font-size:5.5px">47-382-066</div>
</div>

<!-- letterhead, plain -->
<div class="item letter" style="left:210px;top:25px">
  <div class="wordmark top"><span class="dot" style="width:8px;height:8px"></span>Kjelvraket</div>
  <div class="wordmark watermark" style="top:118px"><span class="dot"></span>Kjelvraket</div>
  <div class="letter-footer">
    <span class="tiny">Org nr 873 615 309</span><span class="tiny">8642 Raudvik</span><span class="tiny">47-382-066</span><span class="tiny">www.fjordlast.no</span>
  </div>
</div>

<!-- letterhead, wave -->
<div class="item letter" style="left:445px;top:28px;height:255px">
  <div class="wordmark top"><span class="dot" style="width:8px;height:8px"></span>Kjelvraket</div>
  <div class="wordmark watermark" style="top:188px"><span class="dot"></span>Kjelvraket</div>
  <svg class="wave" viewBox="0 0 196 42" height="42" preserveAspectRatio="none" aria-hidden="true">
    <path d="M0 30 C60 8 120 34 196 4 L196 42 L0 42Z" fill="var(--navy)"/>
    <path d="M0 24 C60 4 120 28 196 0" stroke="var(--blue)" stroke-width="1.4" fill="none"/>
    <path d="M0 33 C60 14 120 38 196 9" stroke="#fff" stroke-width="0.8" fill="none"/>
  </svg>
  <div class="wave-contact"><span class="tiny white">Org nr 873 615 309</span><span class="tiny white">8642 Raudvik</span><span class="tiny white">47-382-066</span><span class="tiny white">www.fjordlast.no</span></div>
</div>

<!-- fax -->
<div class="item letter fax" style="left:678px;top:30px">
  <div class="wordmark"><span class="dot" style="width:7px;height:7px"></span>Kjelvraket</div>
  <div class="head-contact"><span class="tiny">8642 Raudvik</span><span class="tiny">47-382-066</span><span class="tiny">www.fjordlast.no</span></div>
  <h1>FAX</h1>
  <div class="fax-fields">
    <span>To :</span><span>From :</span><span>Fax :</span><span>Pages :</span><span>Phone :</span><span>Date :</span><span>Re :</span><span>CC :</span>
  </div>
  <div class="fax-checks"><span>Urgent</span><span>For Review</span><span>Please Comment</span><span>Please Reply</span><span>Please Recycle</span></div>
  <svg class="wave" viewBox="0 0 196 34" height="34" preserveAspectRatio="none" aria-hidden="true">
    <path d="M0 26 C60 6 120 30 196 4 L196 34 L0 34Z" fill="var(--navy)"/>
    <path d="M0 20 C60 2 120 24 196 0" stroke="var(--blue)" stroke-width="1.4" fill="none"/>
    <path d="M0 29 C60 11 120 34 196 8" stroke="#fff" stroke-width="0.8" fill="none"/>
  </svg>
  <span class="tiny white" style="position:absolute;left:146px;bottom:7px">Org nr 873 615 309</span>
</div>

<!-- envelope back -->
<div class="item envelope" style="left:918px;top:28px;height:140px">
  <svg width="217" height="140" viewBox="0 0 217 140" aria-hidden="true" style="position:absolute;left:0;top:0">
    <path d="M0 0 H217 V12 L108 38 L0 12Z" fill="var(--blue)"/>
    <path d="M0 62 L108 90 L217 62 V112 L108 84 L0 112Z" fill="var(--navy)"/>
  </svg>
</div>

<!-- envelope front, wave -->
<div class="item envelope" style="left:918px;top:170px;height:98px">
  <div class="wordmark" style="position:absolute;top:12px;left:8px;font-size:11px"><span class="dot" style="width:7px;height:7px"></span>Kjelvraket</div>
  <svg class="wave" viewBox="0 0 217 36" height="36" preserveAspectRatio="none" aria-hidden="true">
    <path d="M0 30 C70 10 140 30 217 2 L217 36 L0 36Z" fill="var(--navy)"/>
    <path d="M0 24 C70 4 140 24 217 -2" stroke="var(--blue)" stroke-width="1.4" fill="none"/>
    <path d="M0 33 C70 15 140 35 217 7" stroke="#fff" stroke-width="0.8" fill="none"/>
  </svg>
  <div class="wave-contact" style="bottom:12px"><span class="tiny white">Org nr 873 615 309</span><span class="tiny white">8642 Raudvik</span><span class="tiny white">47-382-066</span><span class="tiny white">www.fjordlast.no</span></div>
</div>

<!-- envelope, plain -->
<div class="item envelope" style="left:918px;top:288px;height:95px">
  <div class="wordmark" style="position:absolute;top:9px;left:8px;font-size:11px"><span class="dot" style="width:7px;height:7px"></span>Kjelvraket</div>
  <span class="tiny" style="position:absolute;top:30px;left:9px">8642 Raudvik</span>
  <span class="tiny" style="position:absolute;bottom:5px;left:9px">www.fjordlast.no</span>
</div>

<!-- business card, front with details -->
<div class="item card front" style="left:207px;top:313px">
  <div class="wordmark"><span class="dot" style="width:7px;height:7px"></span>Kjelvraket</div>
  <div class="name">Leif Brattvoll</div>
  <span class="tiny" style="position:absolute;top:46px;left:8px">8642 Raudvik</span>
  <svg class="wave" viewBox="0 0 139 30" height="30" preserveAspectRatio="none" aria-hidden="true">
    <path d="M0 28 C40 10 90 24 139 2 L139 30 L0 30Z" fill="var(--navy)"/>
    <path d="M0 24 C40 6 90 20 139 -2" stroke="var(--blue)" stroke-width="1.2" fill="none"/>
    <path d="M0 30 C40 14 90 28 139 6" stroke="#fff" stroke-width="0.7" fill="none"/>
  </svg>
  <div style="position:absolute;right:6px;top:22px;display:flex;flex-direction:column;gap:1px">
    <span class="tiny">47-382-066</span><span class="tiny">8642 Raudvik</span><span class="tiny">Leif@fjordlast.no</span><span class="tiny">www.fjordlast.no</span>
  </div>
  <span class="tiny white" style="position:absolute;right:6px;bottom:4px">Org nr 873 615 309</span>
</div>

<!-- business card backs -->
<div class="item card" style="left:389px;top:313px">
  <div class="wordmark" style="font-size:13px"><span class="dot" style="width:8px;height:8px"></span>Kjelvraket</div>
  <div class="url">www.fjordlast.no</div>
</div>
<div class="item card blue" style="left:569px;top:313px">
  <div class="wordmark light" style="font-size:13px"><span class="dot" style="width:8px;height:8px"></span>Kjelvraket</div>
  <div class="url">www.fjordlast.no</div>
</div>
<div class="item card navy" style="left:748px;top:313px">
  <div class="wordmark light" style="font-size:13px"><span class="dot" style="width:8px;height:8px"></span>Kjelvraket</div>
  <div class="url">www.fjordlast.no</div>
</div>

</body>
</html>
```